sydney wedding photography business needs a business card design

we need a business card design for a sydney based wedding photography and videography business. our business name is :golden hour studio and film. our target clients are 24-35 yrs female. our style is candid, organic, natural, dynamic. we are a team of young photographers and videographers, and help brides to create memories that they will cherish for the rest of their lives. the logo will be provided. we want an elegant design that reflects our style, and also want to give a great impression to our clients that we are one of the best studios in sydney and our brand means quality and premium service.

Target Market(s)

bride to be, 24-35 years old, living in sydney and surrunding areas

Industry/Entity Type

Wedding Photography

Contact Information for Business Card

address: 57 tarrant street, glenmore nsw 2047
mobile: 0431872259
phone: (02) 9163 2408
info@tidewillowstudio.net.au
www.tidewillowstudio.net.au
facebook:tidewillowweddings
instagram:tidewillowweddings

Font styles to use
Serif
Sans Serif

Requirements
Nice to have
• maybe add my slogan"memories beyond eternity" if the layout looks good
Should not have
• no black color, not good idea for wedding biz card

```html
<!DOCTYPE html>
<html lang="en">
<head>
<meta charset="utf-8">
<title>Golden Hour Studio and Film – Business Card</title>
<link rel="stylesheet" href="https://fonts.googleapis.com/css2?family=Montserrat:wght@400;500;700&display=swap">
<style>
  :root {
    --backdrop: #e9e4da;
    --panel: #fbf6ea;
    --panel-edge: #efe4cc;
    --text: #4a3624;
    --gold: #c9961a;
    --gold-deep: #c38f12;
    --gold-light: #f3cb2a;
    --gold-mid: #e2b21c;
    --card-w: 760px;
    --card-h: 434px;
  }
  * { box-sizing: border-box; margin: 0; padding: 0; }
  html, body {
    width: 1200px;
    height: 950px;
    overflow: hidden;
    background: var(--backdrop);
    font-family: "Montserrat", Arial, sans-serif;
  }
  .canvas {
    position: relative;
    width: 1200px;
    height: 950px;
  }
  .card {
    position: absolute;
    width: var(--card-w);
    height: var(--card-h);
    overflow: hidden;
    box-shadow: 0 12px 28px rgba(90, 70, 40, 0.25);
  }

  /* Back of card */
  .card-back {
    left: 80px;
    top: 40px;
    background: linear-gradient(135deg, var(--panel) 0%, var(--panel-edge) 100%);
  }
  .back-brand {
    position: absolute;
    left: 0;
    right: 0;
    top: 150px;
    text-align: center;
    color: var(--gold);
    font-weight: 700;
    font-size: 26px;
    letter-spacing: 0.5px;
  }
  .back-rule {
    position: absolute;
    left: 0;
    top: 0;
  }
  .back-handle {
    position: absolute;
    left: 0;
    right: 0;
    top: 300px;
    text-align: center;
    color: var(--text);
    font-weight: 500;
    font-size: 15px;
    letter-spacing: 0.3px;
  }

  /* Front of card */
  .card-front {
    left: 360px;
    top: 476px;
    background: linear-gradient(135deg, var(--gold-deep) 0%, var(--gold-light) 45%, var(--gold-mid) 100%);
  }
  .front-shape {
    position: absolute;
    left: 0;
    top: 0;
  }
  .front-brand {
    position: absolute;
    left: 330px;
    right: 20px;
    top: 180px;
    text-align: center;
    color: var(--gold);
    font-weight: 700;
    font-size: 23px;
    letter-spacing: 0.4px;
  }
  .holder {
    position: absolute;
    left: 40px;
    top: 140px;
    color: var(--text);
  }
  .holder-name {
    font-weight: 700;
    font-size: 21px;
  }
  .holder-role {
    font-weight: 500;
    font-size: 15px;
    margin-top: 4px;
  }
  .contact {
    position: absolute;
    left: 40px;
    top: 262px;
    color: var(--text);
    font-size: 14px;
    font-weight: 500;
    line-height: 20px;
    list-style: none;
  }
  .contact li {
    display: flex;
    align-items: center;
    gap: 8px;
  }
  .contact svg {
    width: 13px;
    height: 13px;
    flex: none;
    fill: var(--text);
  }
</style>
</head>
<body>
<main class="canvas">

  <section class="card card-back" aria-label="Business card, back">
    <p class="back-brand">golden hour studio and film</p>
    <svg class="back-rule" width="760" height="434" viewBox="0 0 760 434" aria-hidden="true">
      <line x1="170" y1="276" x2="360" y2="276" stroke="var(--gold)" stroke-width="1.5"/>
      <line x1="400" y1="276" x2="590" y2="276" stroke="var(--gold)" stroke-width="1.5"/>
      <circle cx="370" cy="276" r="6" fill="var(--gold)"/>
      <circle cx="390" cy="276" r="6" fill="var(--gold)"/>
    </svg>
    <p class="back-handle">tidewillowweddings</p>
  </section>

  <section class="card card-front" aria-label="Business card, front">
    <svg class="front-shape" width="760" height="434" viewBox="0 0 760 434" aria-hidden="true">
      <polygon points="300,0 232,190 480,434 760,434 760,0" fill="var(--panel)"/>
      <polyline points="282,0 212,192 458,434" fill="none" stroke="var(--text)" stroke-width="3"/>
    </svg>
    <p class="front-brand">golden hour studio and film</p>

    <div class="holder">
      <p class="holder-name">Mara Ellison</p>
      <p class="holder-role">President</p>
    </div>

    <ul class="contact">
      <li>57 tarrant street</li>
      <li>glenmore nsw 2047</li>
      <li>
        <svg viewBox="0 0 16 16"><path d="M3.5 1.5l3 3-1.6 1.8a9 9 0 0 0 4.8 4.8l1.8-1.6 3 3-2 2C7 14 2 9 1.5 3.5z"/></svg>
        (02) 9163 2408
      </li>
      <li>
        <svg viewBox="0 0 16 16"><path d="M4.5 0.5h7a1 1 0 0 1 1 1v13a1 1 0 0 1-1 1h-7a1 1 0 0 1-1-1v-13a1 1 0 0 1 1-1zm0.8 2v9.5h5.4V2.5zM8 12.8a0.9 0.9 0 1 0 0 1.8 0.9 0.9 0 0 0 0-1.8z"/></svg>
        (04) 3187 2259
      </li>
      <li>
        <svg viewBox="0 0 16 16"><path d="M1 3h14v10H1zm1.5 1.5v0.4L8 9l5.5-4.1v-0.4zM2.5 6.8v4.7h11V6.8L8 10.9z"/></svg>
        info@tidewillowstudio.net.au
      </li>
      <li>
        <svg viewBox="0 0 16 16"><circle cx="8" cy="8" r="7"/><path d="M1.5 8h13M8 1.2c2.2 2 2.2 11.6 0 13.6M8 1.2c-2.2 2-2.2 11.6 0 13.6" stroke="var(--gold-light)" stroke-width="1" fill="none"/></svg>
        tidewillowstudio.net.au
      </li>
    </ul>
  </section>

</main>
</body>
</html>
```